Tamsorellium we are a young innovative brand about making life easier for people with a disability

Our tag line is Making Life Easy, we are still a relatively new company trying to bring innovation and excitement into the disability space - with latest products and technology - we do have existing website but need to unpgrade for a stronger visual presence.

```html
<!DOCTYPE html>
<html lang="en">
<head>
<meta charset="utf-8">
<title>Tamsorellium – Making Life Easy</title>
<link href="https://fonts.googleapis.com/css2?family=Montserrat:wght@400;500;600;700&display=swap" rel="stylesheet">
<style>
:root{
  --red:#e10a0a;
  --dark:#000;
  --ink:#1a1a1a;
  --brown:#2a0f0a;
  --white:#fff;
  --line:#d6d6d6;
}
*{box-sizing:border-box;margin:0;padding:0}
html,body{width:1200px;height:2445px;overflow:hidden;background:var(--white);font-family:'Montserrat',sans-serif;color:var(--ink)}
.page{position:relative;width:1200px;height:2445px;overflow:hidden}
.abs{position:absolute}
a{color:inherit;text-decoration:none}

.topbar{top:0;left:0;width:1200px;height:33px;background:var(--red);color:var(--white);font-size:12.5px;font-weight:600;display:flex;justify-content:space-between;align-items:center;padding:0 98px}
.nav{top:33px;left:0;width:1200px;height:78px;display:flex;align-items:center;padding:0 99px}
.brand{display:flex;align-items:center;gap:8px;font-weight:700;font-size:17px;color:var(--red);width:224px}
.brand .dot{width:44px;height:44px;border-radius:50%;background:var(--red)}
.menu{display:flex;gap:17px;font-size:12.5px;font-weight:500;margin-left:0}
.search{margin-left:38px;width:145px;height:36px;border:1px solid var(--line);border-radius:18px;font-size:10px;display:flex;align-items:center;justify-content:space-between;padding:0 12px}
.cart{margin-left:12px;width:36px;height:36px;border:2px solid var(--dark);border-radius:50%;display:flex;align-items:center;justify-content:center}

.hero{top:111px;left:0;width:1200px;height:395px;background:linear-gradient(100deg,#d9d2c4 0%,#b9a07a 35%,#8a6a33 60%,#5a3f1a 80%,#3a2a12 100%)}
.hero-title{top:176px;left:665px;color:var(--white);font-size:47px;font-weight:700;line-height:59px}
.btn{display:inline-flex;align-items:center;justify-content:center;border-radius:28px;font-weight:700}
.btn-red{background:var(--red);color:var(--white)}
.hero .btn{position:absolute}

.section-title{font-size:35px;font-weight:600;color:var(--brown)}
.cat{width:150px;height:175px;background:var(--white);border-radius:6px;box-shadow:0 2px 6px rgba(0,0,0,.15);overflow:hidden}
.cat-head{height:54px;background:var(--dark);color:var(--white);font-size:16px;font-weight:600;display:flex;align-items:center;justify-content:center;text-align:center;line-height:19px}
.cat.active .cat-head{background:var(--red)}
.cat-img{margin:16px auto 0;width:100px;height:88px;border-radius:4px}
.arrow{width:40px;height:40px;border-radius:50%;background:var(--white);box-shadow:0 2px 6px rgba(0,0,0,.25);display:flex;align-items:center;justify-content:center}

.band{top:922px;left:0;width:1200px;height:489px;background:linear-gradient(90deg,#1e1a10 0%,#3c321a 40%,#a98840 65%,#d8b26a 80%,#8a6f3c 100%)}
.band h2{position:absolute;top:38px;left:97px;color:var(--white);font-size:40px;font-weight:600;line-height:48px}
.band .copy{position:absolute;top:152px;left:97px;width:520px;color:var(--white);font-size:15.5px;font-weight:500;line-height:21.5px}
.band .copy p{margin-bottom:21px}

.tabs{top:1504px;left:502px;display:flex;gap:38px;font-size:13px;font-weight:500;color:var(--ink)}
.tabs .on{color:var(--red);text-decoration:underline}
.product{width:237px;height:366px;border:1px solid var(--line);border-radius:20px;text-align:center}
.product .pic{margin:30px auto 0;width:190px;height:130px;border-radius:6px;background:linear-gradient(#f2f2f2,#dcdcdc)}
.product h3{margin-top:28px;height:48px;font-size:17px;font-weight:500;line-height:23px}
.product .price{margin-top:18px;font-size:15px;font-weight:500}
.product .btn{margin-top:22px;width:162px;height:45px;border:1.5px solid var(--dark);font-size:17px;font-weight:600}
.product .btn-red{border-color:var(--red)}

.footer{top:2046px;left:0;width:1200px;height:399px;background:var(--dark);color:var(--white)}
.footer h4{position:absolute;top:42px;font-size:26px;font-weight:700}
.fbrand{position:absolute;top:50px;left:103px;display:flex;align-items:center;gap:8px;font-size:17px;font-weight:700}
.fbrand .dot{width:44px;height:44px;border-radius:50%;background:var(--white)}
.pay{position:absolute;font-size:15px;font-weight:600}
.email{position:absolute;top:118px;left:348px;width:237px;height:54px;border:2px solid var(--white);border-radius:6px;font-size:13px;display:flex;align-items:center;padding-left:11px}
.fnav{position:absolute;top:118px;left:630px;font-size:16px;font-weight:500;line-height:25.6px;list-style:none}
.contact{position:absolute;left:856px;font-size:16px;font-weight:500;line-height:21px;display:flex;gap:18px}
.small{position:absolute;left:817px;font-size:11px;font-weight:600;line-height:21px}
</style>
</head>
<body>
<div class="page">

  <div class="abs topbar">
    <span>Registered CSAS Provider &nbsp;/ Sign in or Create an Account</span>
    <span>Healthcare Providers | CSAS | About Us | Contact Us</span>
  </div>

  <header class="abs nav">
    <div class="brand"><span class="dot"></span>Tamsorellium</div>
    <nav class="menu">
      <a>Wheelchairs</a><a>Parts</a><a>Accessories</a><a>Bargain Center</a><a>Online Invoice/Quotes</a><a>Scooters</a>
    </nav>
    <div class="search">Search All Products
      <svg width="10" height="10" viewBox="0 0 10 10"><circle cx="4" cy="4" r="3" fill="none" stroke="#000" stroke-width="1.5"/><line x1="6.2" y1="6.2" x2="9" y2="9" stroke="#000" stroke-width="1.5"/></svg>
    </div>
    <div class="cart">
      <svg width="20" height="18" viewBox="0 0 20 18"><path d="M1 2h3l2 9h10l2-7H5" fill="none" stroke="#e10a0a" stroke-width="2"/><circle cx="8" cy="15" r="1.6" fill="#e10a0a"/><circle cx="15" cy="15" r="1.6" fill="#e10a0a"/></svg>
    </div>
  </header>

  <section class="abs hero" role="img" aria-label="Photo of a person pushing a wheelchair user beside a misty lake with autumn hills">
    <h1 class="abs hero-title" style="top:65px;left:665px">Welcome To<br>Tamsorellium<br>Making Life Easy</h1>
    <a class="btn btn-red" style="top:256px;left:673px;width:162px;height:52px;font-size:17px">Buy Now</a>
  </section>

  <h2 class="abs section-title" style="top:583px;left:0;width:1215px;text-align:center">CATEGORIES</h2>

  <div class="abs arrow" style="top:729px;left:40px"><svg width="10" height="14"><path d="M8 0v14L0 7z" fill="#000"/></svg></div>
  <div class="abs arrow" style="top:727px;left:1115px"><svg width="10" height="14"><path d="M2 0v14l8-7z" fill="#000"/></svg></div>

  <div class="abs cat" style="top:652px;left:99px"><div class="cat-head">Accessories</div><div class="cat-img" role="img" aria-label="Roll of tape" style="background:#d6e6d0"></div></div>
  <div class="abs cat active" style="top:652px;left:269px"><div class="cat-head">Active<br>Wheelchairs</div><div class="cat-img" role="img" aria-label="Active wheelchair" style="background:#e4e4e4"></div></div>
  <div class="abs cat" style="top:652px;left:439px"><div class="cat-head">ArmRests</div><div class="cat-img" role="img" aria-label="Armrest pad" style="background:#e8e8e8"></div></div>
  <div class="abs cat" style="top:652px;left:609px"><div class="cat-head">Axles, Hubs<br>and Parts</div><div class="cat-img" role="img" aria-label="Wheel axle part" style="background:#e6e6e6"></div></div>
  <div class="abs cat" style="top:652px;left:779px"><div class="cat-head">Back</div><div class="cat-img" role="img" aria-label="Wheelchair back cushion" style="background:#dadada"></div></div>
  <div class="abs cat" style="top:652px;left:950px"><div class="cat-head">Bags</div><div class="cat-img" role="img" aria-label="Wheelchair bag" style="background:#dcdcdc"></div></div>

  <section class="abs band" role="img" aria-label="Photo of a laughing child in a wheelchair with his mother in a sunny field">
    <h2>WHEELCHAIRS<br>FOR SALE</h2>
    <div class="copy">
      <p>Are you trying to find the ideal wheelchair? Due to the vast number of possibilities, selecting a simple mobility item like a wheelchair can easily become overwhelming.</p>
      <p>Tamsorellium offers wheelchairs for sale in various sizes, styles, price ranges, and combinations that meet a range of demands and requirements you need.</p>
      <p>Everyone may find wheelchairs at Tamsorellium. We offer manual, power-assist units, and wheelchair accessories for sale and rental.</p>
    </div>
    <a class="btn btn-red" style="position:absolute;top:397px;left:97px;width:162px;height:52px;font-size:17px">Read More</a>
  </section>

  <h2 class="abs section-title" style="top:1496px;left:100px">OUR PRODUCTS</h2>
  <div class="abs tabs"><span class="on">POWER ASSIST UNITS</span><span>BAGS</span><span>BRAKES/LOCKS &amp; COMPONENTS</span><span>MOVACRAFT</span></div>

  <div class="abs arrow" style="top:1753px;left:40px"><svg width="10" height="14"><path d="M8 0v14L0 7z" fill="#000"/></svg></div>
  <div class="abs arrow" style="top:1751px;left:1115px"><svg width="10" height="14"><path d="M2 0v14l8-7z" fill="#000"/></svg></div>

  <div class="abs product" style="top:1582px;left:99px"><div class="pic" role="img" aria-label="Folding wheelchair"></div><h3>GlideLine<br>Roller Replacement Kit</h3><div class="price">$39500</div><a class="btn">Add To Cart</a></div>
  <div class="abs product" style="top:1582px;left:354px"><div class="pic" role="img" aria-label="Power assist handcycle unit"></div><h3>Vector 350 by Orvano</h3><div class="price">$5,85000</div><a class="btn btn-red">Add To Cart</a></div>
  <div class="abs product" style="top:1582px;left:609px"><div class="pic" role="img" aria-label="Red power assist attachment"></div><h3>Emberline by Kestro<br>Motion 2.5</h3><div class="price">$6,25000</div><a class="btn">Add To Cart</a></div>
  <div class="abs product" style="top:1582px;left:863px"><div class="pic" role="img" aria-label="Wheelchair with power attachment"></div><h3>Skyrunner by Kestro<br>Motion</h3><div class="price">£620.00</div><a class="btn">Add To Cart</a></div>

  <footer class="abs footer">
    <div class="fbrand"><span class="dot"></span>Tamsorellium</div>
    <span class="pay" style="top:145px;left:103px">Cardora</span>
    <span class="pay" style="top:145px;left:190px">Paymint</span>
    <span class="pay" style="top:200px;left:103px">Quickpay</span>
    <span class="pay" style="top:200px;left:203px">Vestro</span>

    <h4 style="left:344px">NEWSLETTER</h4>
    <div class="email">EMAIL..</div>
    <a class="btn btn-red" style="position:absolute;top:195px;left:347px;width:136px;height:45px;font-size:14px;font-weight:500">Send Now</a>

    <h4 style="left:621px">NAVIGATIONS</h4>
    <ul class="fnav"><li>Search</li><li>About us</li><li>Privacy Policy</li><li>Postage</li><li>International Shipping</li><li>Terms of Service</li><li>Returns Policy</li></ul>

    <h4 style="left:856px">GET IN TOUCH</h4>
    <div class="contact" style="top:125px"><svg width="12" height="16" viewBox="0 0 12 16"><path d="M6 0a6 6 0 0 1 6 6c0 4-6 10-6 10S0 10 0 6a6 6 0 0 1 6-6z" fill="#fff"/><circle cx="6" cy="6" r="2.2" fill="#000"/></svg><span>14 Harbour Lane,<br>Portvale, 19</span></div>
    <div class="contact" style="top:190px"><svg width="14" height="14" viewBox="0 0 14 14"><path d="M3 0l3 3-2 2c1 2 3 4 5 5l2-2 3 3-2 3C6 14 0 8 0 3z" fill="#fff"/></svg><span>0400 123 456</span></div>
    <div class="contact" style="top:238px"><svg width="15" height="12" viewBox="0 0 15 12"><rect x="1" y="1" width="13" height="10" fill="none" stroke="#fff" stroke-width="1.4"/><path d="M1 1l6.5 5.5L14 1" fill="none" stroke="#fff" stroke-width="1.4"/></svg><span>hello@tamsorellium.com</span></div>

    <div style="position:absolute;top:340px;left:94px;font-size:16px;font-weight:500">© copyrights 2023 Tamsorellium &nbsp;| &nbsp;All Rights Reserved</div>
    <div class="small" style="top:326px">Wheelchairs &nbsp;/ Parts &nbsp;/ Accessories &nbsp;/ Bargain Center<br>Online Invoice/Quotes &nbsp;/ Scooters</div>
  </footer>

</div>
</body>
</html>
```